Sproutwise Website Required

I am looking for someone to develop a website akin to the simplicity of www.boxlantern.example with a video in the center or a tab that permits one to "Accept the Challenge."

Incorporates our logo and is used to promote our "$5 Quest Program."

Please see attachments, but we are igniting entrepreneurial spirit among our nation's youth through this interactive and intensive program!

There should be a way to navigate to other sections of the site including:

About
Why
Request Sproutwise Packet
Success Stories
Partners
Link to Norvik Holdings
Updates

Thanks to all in advance!

Looking forward to working with you!

Good feel of what we are looking for in terms of "feel"

http://www.thebrightripple.example/

Thank you,

RB

Please make note of this website, we are going for a feel that is akin to this and less modern and professional...more abstract and interactive...but of course include space for our video:

Colors, feel, imagery, is great. Keep your formats, but bring on the feel!

Thank you all for your hard work and patience.

Thank you all for your hard work thus far.

Meanwhile, please understand that the Sproutwise is young, youthful, full of challenge and vitality, it is a competition among students from high school and universities.  The websites you have delivered are too corporate, stale, and standard.  I'm looking for something that is fresh, different, like www.thebrightripple.example.

Symbols, cartoonish, but serious, down to business and save the world one $5 bill at a time.  The logo can be used as a theme...the colors, the feel.

Video space for explanation on the Sproutwise front and center.  With leaves, $ signs, colorful colors, etc.

Visual needs to be compelling to Join the Challenge! Although Norvik Holdings and the tree is a parent company; Sproutwise is separate and Norvik Holdings should only be mentioned as a link.

PixelHarbor.example in regard to simplicity; and www.thebrightripple.example in terms of style.

Thank you,

Raphael

Like the designs that have been submitted; we are almost there.

Target Market(s)

Professors, students, teachers, parents and NGO leaders who wish to use our program as a way to inspire leadership/entrepreneurship/fundraise for their causes.

Requirements
Must have
• Place for the video, front and center
Include logo
Forsight for blogging, message, etc.
Nice to have
• Plan "buckets" to include"
Explanation Video
Two pamphlets
Contract
FAQs
Website with Blog, voting, registration, video upload, etc.
Flyer perfected
Parable...symbol of our life
Photos
Stats included
Testimonials
Organizations that have used (TKWLM, North Brook Lodge, Marlowton High)
Sponsors (Open Lantern, Copperleaf Learningfield)
Photos from events

I understand this takes coding and such, but want you to be aware of the long term vision for it!

```html
<!DOCTYPE html>
<html lang="en">
<head>
<meta charset="utf-8">
<title>Sproutwise — Home</title>
<link rel="stylesheet" href="https://fonts.googleapis.com/css2?family=Roboto+Condensed:wght@400;500&family=Arimo:wght@400;700&family=PT+Sans:wght@400&display=swap">
<style>
  :root {
    --page-bg: #fdf6ea;
    --page-bg-deep: #f6ead3;
    --panel-green: #76b38d;
    --ribbon: #fee4b1;
    --ribbon-edge: #f5cf86;
    --nav-text: #555555;
    --nav-active: #1a8a3a;
    --brand-green: #14913c;
    --brand-grey: #555555;
    --text-light: #ffffff;
    --heading-dark: #3c3c3c;
    --ink: #222222;
    --video-face: #c9e6d3;
    --video-frame: #e8f3ec;
    --button-dark: #141414;
    --button-ring: #a7e2bd;
    --footer-text: #333333;
  }
  * { box-sizing: border-box; margin: 0; padding: 0; }
  html, body { width: 1200px; height: 918px; overflow: hidden; }
  body {
    position: relative;
    background: radial-gradient(circle at 30% 20%, var(--page-bg) 0%, var(--page-bg-deep) 120%);
    font-family: "Arimo", Arial, sans-serif;
    color: var(--ink);
  }
  .abs { position: absolute; }

  /* top utility bar */
  .utility { top: 6px; left: 916px; display: flex; align-items: center; font-family: "Roboto Condensed", sans-serif; font-size: 15px; letter-spacing: .5px; color: var(--ink); }
  .utility a { color: inherit; text-decoration: none; margin-right: 22px; }
  .language {
    top: 0; left: 1027px; width: 97px; height: 27px; background: var(--brand-green);
    color: #fff; font-family: "Roboto Condensed", sans-serif; font-size: 13px; font-weight: 500;
    display: flex; align-items: center; padding-left: 8px; gap: 10px; border-radius: 0 0 3px 3px;
  }

  /* header */
  .mascot { top: 6px; left: 278px; width: 72px; height: 166px; background: linear-gradient(#2a2a2a, #111); border-radius: 36px 36px 10px 10px; }
  .hook { width: 12px; height: 40px; top: 4px; }
  .sign {
    top: 22px; left: 346px; width: 455px; height: 142px; background: #fff;
    border: 1px solid #ddd; box-shadow: 0 8px 8px -6px rgba(0,0,0,.35);
    display: flex; align-items: center; justify-content: center;
  }
  .sign-inner { position: absolute; inset: 8px; border: 5px solid var(--ribbon-edge); outline: 1px dashed #fff; outline-offset: -4px; }
  .brand { font-family: "Arimo", sans-serif; font-weight: 700; color: var(--brand-grey); white-space: nowrap; }
  .sign .brand { font-size: 56px; position: relative; }

  /* green stage */
  .stage { top: 182px; left: 57px; width: 1087px; height: 634px; background: var(--panel-green); border-radius: 5px; }

  /* ribbon navigation */
  .ribbon-tail { top: 208px; }
  .ribbon {
    top: 203px; left: 46px; width: 1110px; height: 61px; background: var(--ribbon);
    border-top: 2px solid var(--ribbon-edge); border-bottom: 2px solid var(--ribbon-edge);
    display: flex; align-items: center; justify-content: center;
  }
  .main-nav { display: flex; align-items: center; font-family: "Roboto Condensed", sans-serif; font-size: 20px; letter-spacing: .4px; }
  .main-nav a { color: var(--nav-text); text-decoration: none; text-transform: uppercase; }
  .main-nav a.is-active { color: var(--nav-active); }
  .main-nav .sep { width: 5px; height: 5px; border-radius: 50%; background: var(--nav-active); margin: 0 26px; }

  /* columns */
  .column-title { font-family: "PT Sans", sans-serif; font-weight: 400; font-size: 20px; color: var(--heading-dark); padding-bottom: 10px; border-bottom: 1px dotted #3d5f49; text-shadow: 0 1px 0 rgba(255,255,255,.35); }
  .welcome { top: 303px; left: 79px; width: 291px; }
  .welcome p { color: var(--text-light); font-size: 13.5px; line-height: 20px; text-align: justify; margin-top: 9px; text-shadow: 0 1px 1px rgba(0,0,0,.25); }
  .welcome .column-title { margin-bottom: 14px; text-transform: uppercase; }

  .testimonials { top: 303px; left: 948px; width: 183px; }
  .testimonials .column-title { text-align: right; }
  .quote { position: relative; margin-top: 24px; padding-left: 7px; }
  .quote + .quote { margin-top: 30px; }
  .quote-mark { position: absolute; left: -22px; top: -18px; font-family: Georgia, serif; font-size: 110px; line-height: 1; color: rgba(255,255,255,.12); }
  .quote p { color: var(--text-light); font-size: 13.5px; line-height: 17.5px; text-align: justify; width: 158px; position: relative; text-shadow: 0 1px 1px rgba(0,0,0,.2); }
  .quote cite { display: block; text-align: right; color: var(--text-light); font-style: normal; font-size: 13.5px; margin-top: 9px; }

  /* video */
  .video-frame {
    top: 258px; left: 411px; width: 492px; height: 430px; background: var(--video-frame);
    border-radius: 0 0 8px 8px; padding: 6px; box-shadow: 0 18px 14px -14px rgba(0,0,0,.5);
  }
  .video-face {
    position: relative; width: 100%; height: 100%;
    background: radial-gradient(circle at 50% 40%, #a9d9bb 0%, #8fcaa6 45%, var(--video-face) 100%);
    border: 2px dashed #f4fbf6; border-radius: 0 0 6px 6px;
  }
  .play { position: absolute; left: 155px; top: 79px; }
  .watch-label, .watch-echo { position: absolute; left: 0; right: 0; text-align: center; font-family: "Roboto Condensed", sans-serif; font-weight: 500; font-size: 30px; color: #151515; }
  .watch-label { top: 296px; }
  .watch-echo { top: 326px; transform: scaleY(-1); opacity: .18; }

  .cta {
    top: 727px; left: 490px; width: 306px; height: 64px; border: 3px solid var(--button-ring); border-radius: 4px;
    background: radial-gradient(ellipse at 50% 40%, #4a4a4a 0%, var(--button-dark) 70%);
    color: #fff; font-family: "Roboto Condensed", sans-serif; font-size: 23px; letter-spacing: .3px;
    display: flex; align-items: center; justify-content: center; text-decoration: none; text-transform: uppercase;
  }

  /* footer */
  .footer-rule { top: 834px; left: 68px; width: 1064px; border-top: 3px dotted #e4ddd0; }
  .footer-brand { top: 856px; left: 83px; }
  .footer-brand .brand { font-size: 23px; }
  .footer-nav { top: 855px; right: 82px; display: flex; gap: 18px; font-size: 12px; }
  .footer-nav a { color: var(--footer-text); text-decoration: none; }
  .copyright { top: 880px; right: 82px; font-size: 12px; color: var(--footer-text); }
</style>
</head>
<body>

  <div class="abs utility"><a href="#">FAQ</a><a href="#">SIGNIN</a></div>
  <div class="abs language">LANGUAGE
    <svg width="11" height="9" viewBox="0 0 11 9" aria-hidden="true"><path d="M0 0h11L5.5 9z" fill="#fff"/></svg>
  </div>

  <div class="abs mascot" role="img" aria-label="Silhouette figure leaning on the sign"></div>

  <svg class="abs hook" style="left:377px" viewBox="0 0 12 40" aria-hidden="true"><circle cx="6" cy="6" r="4" fill="none" stroke="#666" stroke-width="2"/><line x1="6" y1="10" x2="6" y2="36" stroke="#777" stroke-width="2"/><circle cx="6" cy="36" r="3" fill="#888"/></svg>
  <svg class="abs hook" style="left:763px" viewBox="0 0 12 40" aria-hidden="true"><circle cx="6" cy="6" r="4" fill="none" stroke="#666" stroke-width="2"/><line x1="6" y1="10" x2="6" y2="36" stroke="#777" stroke-width="2"/><circle cx="6" cy="36" r="3" fill="#888"/></svg>

  <header class="abs sign">
    <div class="sign-inner"></div>
    <div class="brand">Sproutwise</div>
  </header>

  <div class="abs stage"></div>

  <svg class="abs ribbon-tail" style="left:0" width="52" height="66" viewBox="0 0 52 66" aria-hidden="true">
    <path d="M0 2H46V58H0L14 30Z" fill="#fcdda0" stroke="#f5cf86"/>
    <path d="M46 58L57 66V58Z" fill="#1d1d1d"/>
  </svg>
  <svg class="abs ribbon-tail" style="left:1148px" width="52" height="66" viewBox="0 0 52 66" aria-hidden="true">
    <path d="M52 2H6V58H52L38 30Z" fill="#fcdda0" stroke="#f5cf86"/>
    <path d="M6 58L-5 66V58Z" fill="#1d1d1d"/>
  </svg>

  <nav class="abs ribbon">
    <div class="main-nav">
      <a href="#" class="is-active">Home</a><span class="sep"></span>
      <a href="#">About Us</a><span class="sep"></span>
      <a href="#">Why We Are?</a><span class="sep"></span>
      <a href="#">Success Stories</a><span class="sep"></span>
      <a href="#">Partners</a><span class="sep"></span>
      <a href="#">Norvik Holdings</a>
    </div>
  </nav>

  <section class="abs welcome">
    <h2 class="column-title">Welcome to Sproutwise</h2>
    <p>Lorem ipsum dolor sit amet, consectetur adipiscing elit. Curabitur eu nisl odio. Cras egestas turpis in mi feugiat vel tincidunt arcu accumsan. Phasellus non posuere eros. Aenean consectetur.</p>
    <p>sapien in elit luctus ac posuere purus placerat. Aliquam turpis lorem,.</p>
    <p>Donec fermentum sodales erat, quis consequat nisi ornare eget. Duis volutpat justo ut ante imperdiet feugiat. fermentum sodales erat, quis consequat nisi ornare eget. Duis volutpat justo ut ante imperdiet feugiat.</p>
    <p>sapien in elit luctus ac posuere purus placerat. Aliquam turpis lorem,.</p>
  </section>

  <section class="abs video-frame">
    <div class="video-face" role="img" aria-label="Explanation video with soft leaf backdrop">
      <svg class="play" width="160" height="160" viewBox="0 0 160 160" aria-hidden="true">
        <defs>
          <radialGradient id="playFill" cx="50%" cy="35%" r="65%">
            <stop offset="0" stop-color="#3a3a3a"/><stop offset="1" stop-color="#0c0c0c"/>
          </radialGradient>
        </defs>
        <circle cx="80" cy="80" r="80" fill="url(#playFill)"/>
        <path d="M65 46L104 80L65 114Z" fill="#d6d6d6"/>
      </svg>
      <div class="watch-label">WATCH VIDEO</div>
      <div class="watch-echo" aria-hidden="true">WATCH VIDEO</div>
    </div>
  </section>

  <section class="abs testimonials">
    <h2 class="column-title">Client Testimonials</h2>
    <blockquote class="quote">
      <span class="quote-mark" aria-hidden="true">&ldquo;</span>
      <p>Lorem ipsum dolor sit amsectetur adipiscing elit. Curabitur eu nisl odio. dolor sit amsectetur u nisl odio.</p>
      <cite>- LOREM IPSUM</cite>
    </blockquote>
    <blockquote class="quote">
      <span class="quote-mark" aria-hidden="true">&ldquo;</span>
      <p>Lorem ipsum dolor sit amsectetur adipiscing elit. Curabitur eu nisl odio. dolor sit amsectetur u nisl odio.</p>
      <cite>- LOREM IPSUM</cite>
    </blockquote>
  </section>

  <a href="#" class="abs cta">Accept the Challenge</a>

  <div class="abs footer-rule"></div>
  <div class="abs footer-brand"><div class="brand">Sproutwise</div></div>
  <nav class="abs footer-nav">
    <a href="#">Home</a><a href="#">About Us</a><a href="#">Success Stories</a><a href="#">Partners</a><a href="#">Norvik Holdings</a><a href="#">Terms</a><a href="#">Privacy Policy</a>
  </nav>
  <p class="abs copyright">All Rights reserved @ sproutwise</p>

</body>
</html>
```